Business card design for a teacher - double sided, sleek design.

My name is Lina and I am an online Arabic language teacher. I am looking for a beautiful business card design for my online teaching business.

The cards will be printed in 85mm x 55mm size.
The card can be either portrait or landscape.

The design should contain my logo on one side and information on the other.

The design needs to be clean and modern. Use of subtle Arabic geometric patterns would be nice. Icons for the social media information on the card should also match the design theme.

My logo font is Consolas, which is a Monospace font.

Business card design should be delivered with editable PSD or EPS files in the handover.

Thanks

Lina

----

Information on the back:

URL: www.speakwithnadia.net [this should stand out more than other details]
Email: info@speakwithnadia.net
Instagram: @speakwithnadia
Facebook: facebook.com/speakwithnadia
Skype: speakwithnadia

My brand colours are shown in the logo attached. These are:
- Teal green - 4DC9C1
- Mango yellow - FFD600

Target Market(s)

- Young professionals
- Expatriates
- Women and Men

Industry/Entity Type

Education

Contact Information for Business Card

Information on the back:

Skype: speakwithnadia

- Teal green - 4DC9C1
- Mango yellow - FFD600

Font styles to use
Other font styles liked:
• Any font complimentary to my logo font which is a Monospace font called Consolas.

Colors

Designer to choose colors to be used in the design.

Requirements
Must have
• - Aesthetically pleasing look
• - Complimentary design with existing logo
Nice to have
• Arabic geometrical patterns

```html
<!DOCTYPE html>
<html lang="en">
<head>
<meta charset="utf-8">
<title>Speak with Nadia – Business Card</title>
<link href="https://fonts.googleapis.com/css2?family=Roboto:wght@400&display=swap" rel="stylesheet">
<style>
  :root {
    --teal: #55bfb6;
    --paper: #f3f3f3;
    --ink: #4a4a4a;
    --stage: #2a2a2a;
    --white: #ffffff;
  }
  * { margin: 0; padding: 0; box-sizing: border-box; }
  html, body { width: 1200px; height: 960px; overflow: hidden; background: var(--stage); }
  .canvas { position: relative; width: 1200px; height: 960px; }

  .card { position: absolute; width: 600px; height: 343px; overflow: hidden; }
  .card-front { left: 314px; top: 113px; background: var(--paper); }
  .card-back { left: 311px; top: 472px; background: var(--teal); }

  .brand { position: absolute; left: 43px; top: 82px; display: flex; align-items: center; gap: 12px; }
  .brand-dot { width: 16px; height: 16px; border-radius: 50%; background: var(--teal); flex: none; }
  .brand-name { font-family: "Roboto", sans-serif; font-weight: 400; color: var(--ink);
    font-size: 26px; line-height: 1; white-space: nowrap; }

  .contact-list { position: absolute; left: 43px; top: 207px; list-style: none;
    font-family: "Roboto", sans-serif; font-size: 14.5px; color: var(--ink); }
  .contact-list li { display: flex; align-items: center; height: 19px; gap: 8px; }
  .contact-icon { width: 13px; height: 13px; flex: none; }
  .icon-square { background: var(--teal); border-radius: 2px; }

  .front-wave { position: absolute; inset: 0; }

  .back-name { position: absolute; left: 0; right: 0; top: 146px; text-align: center;
    font-family: "Roboto", sans-serif; font-weight: 400; color: var(--white);
    font-size: 30px; line-height: 1; }
  .back-url { position: absolute; left: 0; right: 0; top: 293px; text-align: center;
    font-family: "Roboto", sans-serif; font-size: 13.5px; letter-spacing: 3px; color: var(--white); }
</style>
</head>
<body>
<main class="canvas">

  <section class="card card-front" aria-label="Business card front">
    <svg class="front-wave" width="600" height="343" viewBox="0 0 600 343" role="img" aria-label="Large teal decorative brand shape">
      <path d="M386 0 H600 V343 H440 C330 332 222 300 240 232 C258 170 330 150 342 100 C352 60 368 22 386 0 Z" fill="var(--teal)"/>
    </svg>

    <div class="brand">
      <span class="brand-dot"></span>
      <span class="brand-name">Speak with Nadia</span>
    </div>

    <ul class="contact-list">
      <li>
        <svg class="contact-icon" viewBox="0 0 13 13" aria-hidden="true">
          <rect x="0.5" y="2.5" width="12" height="8" fill="var(--teal)"/>
          <path d="M0.5 2.5 L6.5 7 L12.5 2.5" fill="none" stroke="var(--white)" stroke-width="1"/>
        </svg>
        info@speakwithnadia.net
      </li>
      <li><span class="contact-icon icon-square"></span>@speakwithnadia</li>
      <li><span class="contact-icon icon-square"></span>/speakwithnadia</li>
      <li><span class="contact-icon icon-square"></span>speakwithnadia</li>
      <li>
        <svg class="contact-icon" viewBox="0 0 13 13" aria-hidden="true">
          <circle cx="6.5" cy="6.5" r="6" fill="var(--teal)"/>
          <ellipse cx="6.5" cy="6.5" rx="2.6" ry="6" fill="none" stroke="var(--white)" stroke-width="0.9"/>
          <line x1="0.5" y1="6.5" x2="12.5" y2="6.5" stroke="var(--white)" stroke-width="0.9"/>
        </svg>
        www.speakwithnadia.net
      </li>
    </ul>
  </section>

  <section class="card card-back" aria-label="Business card back">
    <p class="back-name">Speak with Nadia</p>
    <p class="back-url">www.speakwithnadia.net</p>
  </section>

</main>
</body>
</html>
```